Harrow Grading LLC business card design

Excavation company business cards

Contact Information for Business Card

Harrow Grading LLC cell phone 208-417-6290 office phone 208-319-4856 harrowgradingllc@maplecove.com Driveways, site prep, retaining walls, septic systems, rock delivery

Colors

Designer to choose colors to be used in the design.

```html
<!DOCTYPE html>
<html lang="en">
<head>
<meta charset="utf-8">
<title>Harrow Grading LLC — Business Card</title>
<link rel="stylesheet" href="https://fonts.googleapis.com/css2?family=Exo+2:wght@600;700&family=Karla:wght@400;600&display=swap">
<style>
  :root {
    --backdrop: #929292;
    --card-white: #ffffff;
    --card-grey: #676767;
    --brand-orange: #ea6b1f;
    --brand-grey: #6a6a6a;
    --text-grey: #555555;
    --white: #ffffff;
  }
  html, body {
    margin: 0;
    padding: 0;
    width: 1200px;
    height: 1200px;
    overflow: hidden;
    background: var(--backdrop);
  }
  .sheet { position: relative; width: 1200px; height: 1200px; }
  .card {
    position: absolute;
    left: 150px;
    width: 900px;
    height: 514px;
    overflow: hidden;
  }
  .card--front { top: 50px; background: var(--card-white); }
  .card--back { top: 636px; background: var(--card-grey); }

  /* Front */
  .wordmark {
    position: absolute;
    left: 64px;
    top: 120px;
    margin: 0;
    font-family: "Exo 2", sans-serif;
    font-weight: 700;
    color: var(--brand-orange);
    font-size: 66px;
    line-height: 1;
    letter-spacing: 3px;
  }
  .wordmark .sub {
    display: block;
    font-size: 17px;
    letter-spacing: 13.5px;
    margin-top: 10px;
  }
  .contact-list {
    position: absolute;
    left: 64px;
    top: 342px;
    margin: 0;
    padding: 0;
    list-style: none;
    font-family: "Karla", sans-serif;
    font-size: 19px;
    color: var(--text-grey);
    line-height: 26px;
  }
  .contact-list li { display: flex; align-items: center; gap: 10px; }
  .contact-list svg { width: 16px; height: 16px; flex: none; }
  .person {
    position: absolute;
    right: 62px;
    top: 372px;
    text-align: right;
  }
  .person-name {
    margin: 0;
    font-family: "Exo 2", sans-serif;
    font-weight: 600;
    font-size: 31px;
    color: var(--brand-orange);
    line-height: 1.1;
  }
  .person-role {
    margin: 2px 0 0;
    font-family: "Karla", sans-serif;
    font-size: 19px;
    letter-spacing: 1px;
    color: var(--text-grey);
  }
  .footer-band {
    position: absolute;
    left: 0;
    bottom: 0;
    width: 100%;
    height: 20px;
    display: flex;
    gap: 3px;
  }
  .footer-band .band-orange { width: 500px; background: var(--brand-orange); }
  .footer-band .band-grey { flex: 1; background: var(--brand-grey); }

  /* Back */
  .back-wordmark {
    position: absolute;
    left: 69px;
    top: 64px;
    margin: 0;
    font-family: "Exo 2", sans-serif;
    font-weight: 700;
    color: var(--white);
    font-size: 54px;
    line-height: 1;
    letter-spacing: 3px;
  }
  .back-wordmark .sub {
    display: block;
    font-size: 13px;
    letter-spacing: 11px;
    margin-top: 4px;
  }
  .back-url {
    position: absolute;
    left: 69px;
    top: 146px;
    margin: 0;
    font-family: "Karla", sans-serif;
    font-weight: 600;
    font-size: 19px;
    color: var(--white);
    letter-spacing: 0.5px;
  }
  .hero-art {
    position: absolute;
    left: 440px;
    top: 190px;
    right: 0;
    bottom: 0;
    background: linear-gradient(135deg, #6c6c6c 0%, #4a4a4a 55%, #262626 100%);
  }
</style>
</head>
<body>
<main class="sheet">
  <section class="card card--front">
    <h1 class="wordmark">HARROW<span class="sub">GRADING LLC</span></h1>

    <ul class="contact-list">
      <li>
        <svg viewBox="0 0 16 16" aria-hidden="true"><path fill="#ea6b1f" d="M3.5 1.5l2.5 0 1 3.5-1.6 1.2a8 8 0 0 0 4.4 4.4L11 9l3.5 1v2.5c0 1-1 2-2 2C6.5 14.5 1.5 9.5 1.5 3.5c0-1 1-2 2-2z"/></svg>
        <span>208-319-4856</span>
      </li>
      <li>
        <svg viewBox="0 0 16 16" aria-hidden="true"><rect x="4" y="1" width="8" height="14" rx="1.5" fill="none" stroke="#ea6b1f" stroke-width="1.6"/><rect x="7" y="12" width="2" height="1.2" fill="#ea6b1f"/></svg>
        <span>208-417-6290</span>
      </li>
      <li>
        <svg viewBox="0 0 16 16" aria-hidden="true"><rect x="1.5" y="3.5" width="13" height="9" fill="#ea6b1f"/><path d="M1.5 3.5l6.5 5 6.5-5" fill="none" stroke="#fff" stroke-width="1.2"/></svg>
        <span>harrowgradingllc@maplecove.com</span>
      </li>
      <li>
        <svg viewBox="0 0 16 16" aria-hidden="true"><circle cx="8" cy="8" r="6.5" fill="#ea6b1f"/><path d="M1.5 8h13M8 1.5c2.5 2 2.5 11 0 13M8 1.5c-2.5 2-2.5 11 0 13" fill="none" stroke="#fff" stroke-width="1"/></svg>
        <span>www.harrowgradingllc.com</span>
      </li>
    </ul>

    <div class="person">
      <p class="person-name">Daniel Reyes</p>
      <p class="person-role">President</p>
    </div>

    <div class="footer-band"><span class="band-orange"></span><span class="band-grey"></span></div>
  </section>

  <section class="card card--back">
    <h2 class="back-wordmark">HARROW<span class="sub">GRADING LLC</span></h2>
    <p class="back-url">WWW.HARROWGRADINGLLC.COM</p>
    <div class="hero-art" role="img" aria-label="Large embossed illustration of an excavator in front of mountain peaks"></div>
  </section>
</main>
</body>
</html>
```